Website Redesign using existing images, copy etc.

I'm looking for a website redesign/refresh of my current WordPress website. I would like to utilize the same photography, a new photo viewer, and an overall refresh of the entire design. This will need to be WordPress with simple accessibility to make changes as we add additional properties and make updates. We auction luxury real estate and luxury yachts for non-distressed sellers. It needs to be simple, luxurious and with ease of use for both web and especially mobile. www.BrindleHarrow.com

```html
<!DOCTYPE html>
<html lang="en">
<head>
<meta charset="utf-8">
<title>Brindle Harrow — Real Estate &amp; Yachts</title>
<link href="https://fonts.googleapis.com/css2?family=Libre+Baskerville:wght@400;700&family=Montserrat:wght@400;500;600&display=swap" rel="stylesheet">
<style>
:root{
  --ink:#1a1a1a;
  --text:#555;
  --gold:#a8976f;
  --tan:#ab9c7a;
  --pill-text:#a89a78;
  --navy:#1f2a44;
  --footer:#121212;
  --white:#fff;
}
*{box-sizing:border-box;margin:0;padding:0}
html,body{width:1200px;height:3729px;overflow:hidden;background:var(--white)}
body{position:relative;font-family:"Montserrat",sans-serif;color:var(--ink)}
.abs{position:absolute}
.serif{font-family:"Libre Baskerville",serif}
.pill{position:absolute;display:flex;align-items:center;justify-content:center;background:var(--white);border-radius:24px;font-family:"Libre Baskerville",serif;font-size:18px;color:var(--pill-text);border:1.5px solid #d8d0bd;white-space:nowrap}
.pill.dark{color:var(--ink)}

/* hero */
.hero{position:absolute;left:0;top:0;width:1200px;height:642px;overflow:hidden}
.hero-photo{position:absolute;inset:0;background:linear-gradient(180deg,#8a7a86 0%,#b48c7c 18%,#6b6a4c 38%,#3b4b2c 60%,#6e4a3c 85%,#5a3d32 100%)}
.brand{position:absolute;top:16px;left:0;width:1200px;display:flex;justify-content:center;align-items:center;gap:22px;color:var(--white);font-family:"Libre Baskerville",serif;font-size:40px;letter-spacing:16px}
.brand-ring{width:80px;height:80px;border:3px solid var(--white);border-radius:50%}
.nav{position:absolute;top:122px;color:var(--white);font-weight:600;font-size:17px}
.hero-arc{position:absolute;left:206px;top:192px;width:320px;height:320px;border:5px solid rgba(255,255,255,.85);border-radius:50%;border-right-color:transparent}
.hero-title{position:absolute;left:0;width:1200px;text-align:center;color:var(--white);font-family:"Libre Baskerville",serif;font-weight:700;font-size:40px;line-height:50px;white-space:nowrap;text-shadow:0 2px 6px rgba(0,0,0,.35)}

/* about */
.h2{font-family:"Libre Baskerville",serif;font-size:33px;color:var(--ink)}
.sub{font-size:20px;font-weight:500;color:var(--ink)}
.para{font-size:17px;line-height:25.5px;color:var(--text);text-align:justify}

/* sold */
.sold{position:absolute;left:0;top:1164px;width:1200px;height:747px;background:linear-gradient(180deg,#2d3a5a 0%,#1e2a48 50%,#3a3448 100%)}
.sold-tag{position:absolute;color:var(--white);font-family:"Libre Baskerville",serif;white-space:nowrap}

/* featured */
.badge{position:absolute;width:160px;height:160px;border-radius:50%;background:var(--white);border:7px solid #b9ab88;box-shadow:0 3px 8px rgba(0,0,0,.3)}

/* marketed */
.marketed{position:absolute;left:0;top:2432px;width:1200px;height:808px;background:var(--tan)}
.card{position:absolute;top:441px;width:257px;height:275px;background:#f4f1ea;box-shadow:0 2px 6px rgba(0,0,0,.2)}
.card .ph{position:absolute;left:13px;top:13px;right:13px;bottom:13px}
.arrow{position:absolute;width:46px;height:46px;border:2px solid var(--white);border-radius:50%}

/* footer */
.footer{position:absolute;left:0;top:3240px;width:1200px;height:489px;background:var(--footer);color:var(--white)}
.fh{position:absolute;top:132px;font-weight:600;font-size:20px;white-space:nowrap}
.fl{position:absolute;font-size:20px;white-space:nowrap}
.field{position:absolute;left:806px;width:290px;height:50px}
.field .ring{position:absolute;left:0;top:0;width:46px;height:46px;border:2px solid var(--white);border-radius:50%}
.field .line{position:absolute;left:52px;right:0;top:27px;height:1.5px;background:#ccc}
.field span{position:absolute;left:58px;top:2px;font-size:17px}
</style>
</head>
<body>

<section class="hero">
  <div class="hero-photo" role="img" aria-label="Luxury Mediterranean-style estate with palm trees and a brick driveway at dusk"></div>
  <div class="brand"><span>BRINDLE</span><span class="brand-ring"></span><span>HARROW</span></div>
  <a class="nav" style="left:605px">BUY</a>
  <a class="nav" style="left:735px">SELL</a>
  <a class="nav" style="left:850px">ABOUT</a>
  <a class="nav" style="left:1005px">CONTACT</a>
  <div class="hero-arc"></div>
  <div class="hero-title" style="top:276px;word-spacing:14px">BRINDLE HARROW</div>
  <div class="hero-title" style="top:355px">REAL ESTATE &amp; YACHTS</div>
  <svg class="abs" style="left:234px;top:358px" width="44" height="44" viewBox="0 0 44 44" fill="none" stroke="#fff" stroke-width="2"><circle cx="22" cy="22" r="20"/><path d="M11 23 22 13 33 23M15 20v11h14V20"/></svg>
  <svg class="abs" style="left:922px;top:354px" width="46" height="50" viewBox="0 0 46 50" fill="none" stroke="#fff" stroke-width="2"><path d="M23 4v34M23 8 9 36h14M25 12 37 36H25M5 40h36l-5 6H10z"/></svg>
  <div class="pill" style="left:282px;top:443px;width:309px;height:40px">Browse Upcoming Auctions</div>
  <div class="pill dark" style="left:609px;top:443px;width:310px;height:40px">Browse Past Successes</div>
</section>

<section class="about">
  <h2 class="h2 abs" style="left:113px;top:724px">ABOUT US</h2>
  <div class="sub abs" style="left:111px;top:793px">REAL ESTATE &amp; YACHTS</div>
  <p class="para abs" style="left:113px;top:842px;width:482px">If one were to encounter our team at a social gathering, they would undoubtedly experience an engaging and diverse evening. They would have the opportunity to network with esteemed media executives, enjoy the levity of PR professionals, and engage in thought-provoking discussions</p>
  <div class="pill" style="left:113px;top:1032px;width:208px;height:43px">View More</div>
  <svg class="abs" style="left:1020px;top:664px" width="64" height="74" viewBox="0 0 64 74" fill="none" stroke="#222" stroke-width="2"><path d="M32 4v52M32 10 12 52h20M35 16l18 36H35M4 58h56l-7 10H11z"/></svg>
  <div class="abs" style="left:705px;top:720px;width:318px;height:318px;border:6px solid #e6e6e6;border-radius:50%;box-shadow:0 2px 6px rgba(0,0,0,.15)"></div>
  <div class="abs" role="img" aria-label="Soft palm frond shadow" style="left:1095px;top:900px;width:105px;height:140px;background:linear-gradient(135deg,rgba(200,200,200,0),rgba(190,190,190,.6));border-radius:60px 0 0 0"></div>
</section>

<section class="sold">
  <h2 class="serif abs" style="left:0;top:68px;width:1200px;text-align:center;color:var(--white);font-size:33px;white-space:nowrap">SOLD BY BRINDLE HARROW</h2>
  <p class="abs" style="left:120px;top:130px;width:960px;text-align:center;color:var(--white);font-size:15.5px;line-height:24px">Brindle Harrow is a top-tier destination for luxury property auctions, having overseen the auction marketing of numerous<br>high-end estates and yachts. Our team of luxury home auction experts is committed to helping property owners obtain the<br>best value for their assets while ensuring a timely sale.</p>
  <div class="pill" style="left:496px;top:221px;width:209px;height:42px">View More</div>
  <div class="abs" role="img" aria-label="Aerial view of a wooded estate in Johns Creek, GA" style="left:0;top:346px;width:560px;height:255px;background:linear-gradient(135deg,#5c7a2c,#8c9a4a 45%,#b9a36a 70%,#6a8a34)"></div>
  <div class="sold-tag" style="left:14px;top:516px;font-size:11px;letter-spacing:2px">JOHNS CREEK | GA</div>
  <div class="sold-tag" style="left:14px;top:530px;font-size:36px;letter-spacing:8px">SOLD</div>
  <div class="sold-tag" style="left:14px;top:580px;font-size:12px">BRINDLE HARROW</div>
  <div class="abs" role="img" aria-label="Aerial view of a waterfront home with pool and boat dock in Sarasota, FL" style="left:492px;top:302px;width:708px;height:343px;border-radius:172px 0 0 172px;background:linear-gradient(160deg,#dfe3dc 0%,#6f9a3a 30%,#4a7a2a 55%,#3a5a3a 75%,#5a7a6a 100%);border:8px solid #2a2a2a;border-right:none"></div>
  <div class="sold-tag" style="left:978px;top:555px;font-size:14px;letter-spacing:4px">SARASOTA | FL</div>
  <div class="sold-tag" style="left:976px;top:570px;font-size:46px;letter-spacing:8px">SOLD</div>
  <div class="sold-tag" style="left:978px;top:624px;font-size:17px">BRINDLE HARROW</div>
</section>

<section class="featured">
  <h2 class="h2 abs" style="left:600px;top:1993px;width:487px;text-align:right">AS FEATURED IN</h2>
  <div class="badge" style="left:60px;top:2033px"></div>
  <div class="badge" style="left:238px;top:2033px"></div>
  <div class="badge" style="left:419px;top:2033px"></div>
  <div class="badge" style="left:154px;top:2187px"></div>
  <div class="badge" style="left:334px;top:2187px"></div>
  <p class="para abs" style="left:600px;top:2065px;width:487px;text-align:right;font-size:16.5px">By offering top-tier properties and vessels globally, along with strategic auction dates, exceptional marketing tactics, and a diligent public relations team, even the most prominent media outlets have taken notice. Check out some of our latest press features.</p>
  <div class="pill" style="left:877px;top:2238px;width:210px;height:42px">View More</div>
  <div class="serif abs" style="left:0;top:2350px;width:1200px;text-align:center;font-size:58px;letter-spacing:30px;color:#f1f1f1;white-space:nowrap">BRINDLE HARROW</div>
</section>

<section class="marketed">
  <h2 class="h2 abs" style="left:0;top:86px;width:1200px;text-align:center;line-height:44px">OVER ONE BILLION DOLLARS OF<br>AUCTIONS MARKETED</h2>
  <div class="sub abs" style="left:0;top:196px;width:1200px;text-align:center">REAL ESTATE &amp; YACHTS</div>
  <p class="abs" style="left:0;top:257px;width:1200px;text-align:center;font-size:17px;line-height:26px;color:var(--ink)">If one were to encounter our team at a social gathering, they would undoubtedly<br>experience an engaging and diverse evening.</p>
  <div class="pill" style="left:496px;top:347px;width:209px;height:42px">View More</div>
  <div class="card" style="left:0"><div class="ph" role="img" aria-label="Aerial view of a waterfront peninsula estate" style="background:linear-gradient(180deg,#8aa6c4,#4a6a4a 45%,#2a4a6a)"></div></div>
  <div class="card" style="left:314px"><div class="ph" role="img" aria-label="Bedroom with navy walls and a ceiling fan" style="background:linear-gradient(135deg,#2c3e6e,#e8e2d8 55%,#8a5a3a)"></div></div>
  <div class="card" style="left:628px"><div class="ph" role="img" aria-label="White motor yacht on the water" style="background:linear-gradient(180deg,#e4e8ee,#f6f6f6 45%,#9aa6b2)"></div></div>
  <div class="card" style="left:942px"><div class="ph" role="img" aria-label="Navy-hulled luxury yacht at the dock" style="background:linear-gradient(180deg,#7aa2d8,#d8dde4 40%,#1e2a44 70%,#3a4a6a)"></div></div>
  <div class="pill" style="left:72px;top:558px;width:207px;height:43px">Real Estate</div>
  <div class="pill" style="left:918px;top:558px;width:205px;height:43px">Yachts</div>
  <div class="arrow" style="left:23px;top:556px"><svg width="42" height="42" viewBox="0 0 42 42" fill="none" stroke="#fff" stroke-width="2"><path d="M24 13l-8 8 8 8"/></svg></div>
  <div class="arrow" style="left:1131px;top:556px"><svg width="42" height="42" viewBox="0 0 42 42" fill="none" stroke="#fff" stroke-width="2"><path d="M18 13l8 8-8 8"/></svg></div>
</section>

<footer class="footer">
  <div class="abs" style="left:111px;top:12px;width:86px;height:86px;border:2px solid var(--gold);border-radius:50%"></div>
  <div class="abs" style="left:555px;top:12px;width:90px;height:90px;border:3px solid var(--white);border-radius:50%"></div>
  <div class="abs" role="img" aria-label="Globe illustration" style="left:1003px;top:14px;width:86px;height:86px;border-radius:50%;background:radial-gradient(circle at 40% 40%,#5aa2ee,#2a6ac8)"></div>
  <div class="fh" style="left:111px">Follow Along</div>
  <div class="fh" style="left:346px">Quick Links</div>
  <div class="fh" style="left:536px">Other Links</div>
  <div class="fh" style="left:805px">SIGN UP FOR BRINDLE ALERTS</div>
  <a class="fl" style="left:111px;top:175px">Chatterly</a>
  <a class="fl" style="left:116px;top:218px">Snapfold</a>
  <a class="fl" style="left:116px;top:260px">Workwell</a>
  <a class="fl" style="left:116px;top:303px">Peeplet</a>
  <div class="abs" style="left:118px;top:350px;width:72px;height:92px;background:#4a4a4a;border-radius:36px 36px 8px 8px"></div>
  <a class="fl" style="left:346px;top:175px">Home</a>
  <a class="fl" style="left:346px;top:218px">Buy</a>
  <a class="fl" style="left:351px;top:260px">Sell</a>
  <a class="fl" style="left:351px;top:303px">About</a>
  <a class="fl" style="left:346px;top:346px">Blog</a>
  <a class="fl" style="left:346px;top:389px">Contact</a>
  <a class="fl" style="left:536px;top:175px">Terms Of Services</a>
  <a class="fl" style="left:536px;top:218px">CopyRight Policy</a>
  <a class="fl" style="left:536px;top:260px">Privacy Policy</a>
  <a class="fl" style="left:536px;top:303px">Upcoming Auctions</a>
  <div class="field" style="top:182px"><div class="ring"></div><span>Name</span><div class="line"></div></div>
  <div class="field" style="top:250px"><div class="ring"></div><span>E Mail</span><div class="line"></div></div>
  <div class="pill" style="left:806px;top:321px;width:209px;height:42px;border:none">Submit</div>
  <div class="abs" style="left:0;top:456px;width:1200px;text-align:center;font-size:19px">Copyright @ 2023 - Brindle Harrow - All Rights Reserved</div>
</footer>

</body>
</html>
```